MS Word and MS Powerpoint template creation using existing logo as style guide

Create a professional looking MS Word document template and MS powerpoint template for Torvane Advisory Pty Ltd using a logo that's already been created as the style guide. Torvane is a professional services business providing strategy, governance and execution support to small and medium business, Boards and executive teams. refer design brief.

Target Market(s)

Small to medium business, Chairs, Boards, executive teams, general managers

Industry/Entity Type

Professional business services, consultancy, business support outsourcing

Other font styles liked:
• calibri

Requirements
Must have
• leverage the existing logo for colour scheme. Use the TORVANE logo type font. Fully editable templates Word and MS Powerpoint,
Nice to have
• Refer to the design brief
Should not have
• animations, cartoons, stock images of people.

```html
<!DOCTYPE html>
<html lang="en">
<head>
<meta charset="utf-8">
<title>Torvane Advisory – Strategic Review &amp; Execution Roadmap slide set</title>
<link rel="stylesheet" href="https://fonts.googleapis.com/css2?family=Archivo:wdth,wght@62..125,400..900&display=swap">
<style>
:root{
  --stage:#a6a6a6;
  --deep:#1c2e38;
  --deep-2:#233a45;
  --navy:#1d3550;
  --indigo:#222f6b;
  --paper:#f3f3f3;
  --white:#ffffff;
  --accent:#8fb0cc;
  --mist:#c9d7e3;
  --ink:#16232c;
}
*{margin:0;padding:0;box-sizing:border-box}
html,body{width:1200px;height:927px;overflow:hidden;background:var(--stage)}
body{position:relative;font-family:"Archivo",Arial,sans-serif;color:var(--ink)}
.slide{position:absolute;width:262px;height:148px;overflow:hidden;background:var(--paper)}
.slide.dark{background:linear-gradient(135deg,var(--deep) 0%,var(--deep-2) 60%,var(--deep) 100%);color:var(--white)}
.slide.portrait{width:134px;height:172px}
.a{position:absolute}
.tx{position:absolute;font-size:2.6px;line-height:3.4px;color:#333}
.dark .tx{color:#dfe7ec}
.wide{font-stretch:115%}
.rule{position:absolute;height:1px;background:var(--accent)}
.frame{position:absolute;border:1px solid var(--indigo)}
.wave{position:absolute;background:radial-gradient(ellipse at center,rgba(143,176,204,.45),rgba(143,176,204,0) 70%)}
.photo{position:absolute}
.h{position:absolute;font-weight:700;line-height:1}
.num{position:absolute;font-size:10px;font-weight:500;text-align:center;width:40px}
.lbl{position:absolute;font-size:2.8px;line-height:3.4px;text-align:center;width:40px;color:#cfd9df}
.cell{position:absolute;background:var(--white);color:var(--indigo);font-size:3.4px;font-weight:700;display:flex;align-items:center;justify-content:center}
.card{position:absolute;background:var(--white);color:var(--ink)}
.dot{position:absolute;width:4px;height:4px;border-radius:50%;background:var(--indigo)}
.numbox{position:absolute;width:11px;height:11px;background:var(--indigo);color:#fff;font-size:7px;display:flex;align-items:center;justify-content:center}
.icon{position:absolute;width:28px;height:28px;border-radius:50%;background:radial-gradient(circle at 40% 35%,#3a5a9a,var(--indigo));box-shadow:0 0 0 1.5px #c4cfe6}
</style>
</head>
<body>

<!-- Row 1 -->
<section class="slide dark" style="left:28px;top:43px">
  <p class="a wide" style="left:15px;top:11px;font-size:7px;letter-spacing:1.6px">TORVANE</p>
  <p class="a" style="left:22px;top:41px;font-size:10.5px;letter-spacing:.3px">STRATEGIC REVIEW &amp;</p>
  <p class="h wide" style="left:22px;top:52px;font-size:21px;line-height:19px">Execution<br>Roadmap</p>
  <div class="a" style="left:22px;top:99px;width:136px;height:1px;background:#fff"></div>
  <p class="a" style="left:22px;top:104px;font-size:3.6px;font-weight:700">Connecting Strategy, Governance &amp; Execution</p>
</section>

<section class="slide dark" style="left:312px;top:43px">
  <p class="a wide" style="left:0;width:262px;text-align:center;top:20px;font-size:13px;letter-spacing:3.5px;font-weight:600">AGENDA</p>
  <div class="a" style="left:55px;top:40px;width:151px;height:1px;background:#fff"></div>
  <p class="num" style="left:48px;top:47px">01</p><p class="lbl" style="left:48px;top:61px">Executive<br>Summary</p>
  <p class="num" style="left:89px;top:47px">02</p><p class="lbl" style="left:89px;top:61px">About Torvane<br>Management</p>
  <p class="num" style="left:131px;top:47px">03</p><p class="lbl" style="left:131px;top:61px">Context<br>Problem / Opportunity</p>
  <p class="num" style="left:173px;top:47px">04</p><p class="lbl" style="left:173px;top:61px">Objectives &amp;<br>Success Criteria</p>
  <p class="num" style="left:48px;top:77px">05</p><p class="lbl" style="left:48px;top:91px">Strategic Options<br>Considered</p>
  <p class="num" style="left:89px;top:77px">06</p><p class="lbl" style="left:89px;top:91px">Recommended<br>Solution</p>
  <p class="num" style="left:131px;top:77px">07</p><p class="lbl" style="left:131px;top:91px">Risks &amp;<br>Mitigations</p>
  <p class="num" style="left:173px;top:77px">08</p><p class="lbl" style="left:173px;top:91px">Financial &amp;<br>Resource Impact</p>
  <p class="num" style="left:48px;top:109px">09</p><p class="lbl" style="left:48px;top:123px">Governance &amp;<br>Accountability</p>
  <p class="num" style="left:89px;top:109px">10</p><p class="lbl" style="left:89px;top:123px">Implementation<br>Plan &amp; Timeline</p>
  <p class="num" style="left:131px;top:109px">11</p><p class="lbl" style="left:131px;top:123px">Decision<br>Sought</p>
  <p class="num" style="left:173px;top:109px">12</p><p class="lbl" style="left:173px;top:123px">Next Steps<br>&amp; Q&amp;A</p>
</section>

<section class="slide" style="left:606px;top:43px">
  <div class="wave" role="img" aria-label="Soft flowing line pattern" style="left:-20px;top:0;width:120px;height:148px"></div>
  <div class="a" style="left:126px;top:0;width:136px;height:148px;background:var(--navy)"></div>
  <div class="a" style="left:126px;top:36px;width:136px;height:1px;background:#fff"></div>
  <p class="a" style="left:151px;top:46px;font-size:8.5px;font-weight:600;color:#fff">EXECUTIVE SUMMARY</p>
  <p class="tx" style="left:151px;top:63px;width:84px;color:#d8e2ec">Lorem ipsum dolor sit amet, consectetur adipiscing elit, sed do eiusmod tempor incididunt ut labore et dolore magna aliqua. Ut enim ad minim veniam, quis nostrud exercitation ullamco laboris nisi ut aliquip ex ea commodo consequat. Duis aute irure dolor in reprehenderit in voluptate velit esse cillum dolore eu fugiat nulla pariatur. Excepteur sint occaecat cupidatat non proident, sunt in culpa qui officia deserunt mollit anim id est laborum.</p>
  <div class="rule" style="left:0;top:118px;width:210px"></div>
</section>

<section class="slide dark" style="left:910px;top:43px">
  <div class="a" style="left:0;top:34px;width:262px;height:86px;background:var(--paper)"></div>
  <p class="a" style="left:0;width:113px;text-align:right;top:51px;font-size:11px;font-weight:800;color:var(--ink)">About</p>
  <p class="a" style="left:0;width:113px;text-align:right;top:66px;font-size:7.2px;font-weight:600;color:var(--ink)">TORVANE MANAGEMENT</p>
  <div class="rule" style="left:0;top:79px;width:113px"></div>
  <p class="tx" style="left:130px;top:50px;width:110px;font-size:3.4px;line-height:4.3px">Lorem ipsum dolor sit amet, consectetur adipiscing elit, sed do eiusmod tempor incididunt ut labore et dolore magna aliqua. Ut enim ad minim veniam, quis nostrud exercitation ullamco laboris nisi ut aliquip ex ea commodo consequat. Duis aute irure dolor in reprehenderit in voluptate velit esse cillum dolore eu fugiat nulla pariatur. Excepteur sint occaecat cupidatat non proident, sunt in culpa qui officia deserunt mollit anim id est laborum.</p>
</section>

<!-- Row 2 -->
<section class="slide" style="left:28px;top:211px">
  <div class="wave" role="img" aria-label="Soft flowing line pattern" style="left:-30px;top:60px;width:120px;height:100px"></div>
  <p class="h" style="left:0;width:262px;text-align:center;top:20px;font-size:10px">Principal /</p>
  <p class="h" style="left:0;width:262px;text-align:center;top:30px;font-size:11px;font-weight:600">EXECUTIVE DIRECTOR</p>
  <div class="a" style="left:48px;top:53px;width:171px;height:80px;background:linear-gradient(180deg,#7e93b8,#222f6b 75%)"></div>
  <div class="photo" role="img" aria-label="Team member portrait" style="left:61px;top:47px;width:44px;height:60px;background:linear-gradient(180deg,#79b7e0 55%,#8fb63a 56%)"></div>
  <div class="photo" role="img" aria-label="Team member portrait" style="left:113px;top:47px;width:44px;height:60px;background:linear-gradient(180deg,#79b7e0 55%,#8fb63a 56%)"></div>
  <div class="photo" role="img" aria-label="Team member portrait" style="left:165px;top:47px;width:44px;height:60px;background:linear-gradient(180deg,#79b7e0 55%,#8fb63a 56%)"></div>
  <p class="a" style="left:56px;top:111px;width:54px;text-align:center;font-size:3.6px;font-weight:700;color:#fff">Mara Ellison<br><i style="font-weight:400">Project manager</i></p>
  <p class="a" style="left:108px;top:111px;width:54px;text-align:center;font-size:3.6px;font-weight:700;color:#fff">Dana Kowalczyk<br><i style="font-weight:400">Project manager</i></p>
  <p class="a" style="left:160px;top:111px;width:54px;text-align:center;font-size:3.6px;font-weight:700;color:#fff">Felix Marchetti<br><i style="font-weight:400">Project manager</i></p>
</section>

<section class="slide" style="left:312px;top:211px">
  <div class="wave" role="img" aria-label="Soft flowing line pattern" style="left:-30px;top:-20px;width:90px;height:180px"></div>
  <div class="frame" style="left:23px;top:19px;width:219px;height:109px;background:var(--paper)"></div>
  <p class="h" style="left:0;width:262px;text-align:center;top:33px;font-size:9px">Context:</p>
  <p class="h" style="left:0;width:262px;text-align:center;top:44px;font-size:11.5px;font-weight:600">THE PROBLEM / OPPORTUNITY</p>
  <div class="numbox" style="left:50px;top:65px">01</div>
  <p class="a" style="left:67px;top:64px;font-size:4.5px;font-weight:600">Antivirus protection</p>
  <p class="tx" style="left:67px;top:70px;width:56px;font-size:2.4px;line-height:3px">Lorem ipsum dolor sit amet, consectetur adipiscing elit, sed do eiusmod tempor incididunt ut labore et dolore magna aliqua. Ut enim ad minim</p>
  <div class="numbox" style="left:138px;top:65px">02</div>
  <p class="a" style="left:155px;top:64px;font-size:4.5px;font-weight:600">Technical support</p>
  <p class="tx" style="left:155px;top:70px;width:56px;font-size:2.4px;line-height:3px">Lorem ipsum dolor sit amet, consectetur adipiscing elit, sed do eiusmod tempor incididunt ut labore et dolore magna aliqua. Ut enim ad minim</p>
  <div class="numbox" style="left:50px;top:94px">03</div>
  <p class="a" style="left:67px;top:93px;font-size:4.5px;font-weight:600">Increase computer speed</p>
  <p class="tx" style="left:67px;top:99px;width:56px;font-size:2.4px;line-height:3px">Lorem ipsum dolor sit amet, consectetur adipiscing elit, sed do eiusmod tempor incididunt ut labore et dolore magna aliqua. Ut enim ad minim</p>
  <div class="numbox" style="left:138px;top:94px">04</div>
  <p class="a" style="left:155px;top:93px;font-size:4.5px;font-weight:600">Expert technical services</p>
  <p class="tx" style="left:155px;top:99px;width:56px;font-size:2.4px;line-height:3px">Lorem ipsum dolor sit amet, consectetur adipiscing elit, sed do eiusmod tempor incididunt ut labore et dolore magna aliqua. Ut enim ad minim</p>
</section>

<section class="slide" style="left:610px;top:211px">
  <div class="wave" role="img" aria-label="Soft flowing line pattern" style="left:-40px;top:0;width:80px;height:148px"></div>
  <div class="wave" role="img" aria-label="Soft flowing line pattern" style="left:220px;top:60px;width:80px;height:100px"></div>
  <p class="h" style="left:39px;top:42px;font-size:8px;font-weight:600">Objectives &amp;</p>
  <p class="h wide" style="left:39px;top:51px;font-size:14px;letter-spacing:1.2px;font-weight:600">SUCCESS CRITERIA</p>
  <div class="rule" style="left:39px;top:69px;width:161px"></div>
  <p class="a" style="left:39px;top:73px;font-size:5px;font-weight:600">Objectives</p>
  <p class="a" style="left:131px;top:73px;font-size:5px;font-weight:600">Success Criteria</p>
  <p class="tx" style="left:39px;top:81px;width:84px">Lorem ipsum dolor sit amet, consectetur adipiscing elit, sed do eiusmod tempor incididunt ut labore et dolore magna aliqua. Ut enim ad minim veniam, quis nostrud exercitation ullamco laboris nisi ut aliquip ex ea commodo consequat. Duis aute irure dolor in reprehenderit in voluptate velit esse cillum dolore eu fugiat nulla pariatur. Excepteur sint occaecat cupidatat non proident, sunt in culpa qui officia deserunt mollit anim id est laborum.</p>
  <p class="tx" style="left:131px;top:81px;width:84px">Lorem ipsum dolor sit amet, consectetur adipiscing elit, sed do eiusmod tempor incididunt ut labore et dolore magna aliqua. Ut enim ad minim veniam, quis nostrud exercitation ullamco laboris nisi ut aliquip ex ea commodo consequat. Duis aute irure dolor in reprehenderit in voluptate velit esse cillum dolore eu fugiat nulla pariatur. Excepteur sint occaecat cupidatat non proident, sunt in culpa qui officia deserunt mollit anim id est laborum.</p>
</section>

<section class="slide" style="left:904px;top:211px">
  <div class="wave" role="img" aria-label="Soft flowing line pattern" style="left:200px;top:-20px;width:100px;height:190px"></div>
  <div class="frame" style="left:23px;top:19px;width:220px;height:109px"></div>
  <p class="h" style="left:43px;top:42px;font-size:9px;font-weight:800">Strategic</p>
  <p class="a" style="left:43px;top:52px;font-size:4.8px;font-weight:600;letter-spacing:.3px">OPTIONS CONSIDERED</p>
  <div class="rule" style="left:0;top:63px;width:115px"></div>
  <p class="tx" style="left:43px;top:70px;width:66px">Lorem ipsum dolor sit amet, consectetur adipiscing elit, sed do eiusmod tempor incididunt ut labore et dolore magna aliqua. Ut enim ad minim veniam, quis nostrud exercitation ullamco laboris nisi ut aliquip ex ea commodo consequat. Duis aute irure dolor in reprehenderit in voluptate velit esse cillum dolore eu fugiat nulla pariatur.</p>
  <div class="a" style="left:124px;top:38px;width:1px;height:76px;background:var(--indigo)"></div>
  <div class="dot" style="left:122.5px;top:36px"></div>
  <div class="dot" style="left:122.5px;top:64px"></div>
  <div class="dot" style="left:122.5px;top:92px"></div>
  <p class="a" style="left:130px;top:34px;font-size:6px">Option 1</p>
  <p class="tx" style="left:130px;top:44px;width:100px;font-size:2.3px;line-height:3px">Lorem ipsum dolor sit amet, consectetur adipiscing elit, sed do eiusmod tempor incididunt ut labore et dolore magna aliqua. Ut enim ad minim veniam, quis nostrud exercitation ullamco laboris nisi ut aliquip ex ea commodo consequat.</p>
  <p class="a" style="left:130px;top:62px;font-size:6px">Option 2</p>
  <p class="tx" style="left:130px;top:72px;width:100px;font-size:2.3px;line-height:3px">Lorem ipsum dolor sit amet, consectetur adipiscing elit, sed do eiusmod tempor incididunt ut labore et dolore magna aliqua. Ut enim ad minim veniam, quis nostrud exercitation ullamco laboris nisi ut aliquip ex ea commodo consequat.</p>
  <p class="a" style="left:130px;top:90px;font-size:6px">Option 3</p>
  <p class="tx" style="left:130px;top:100px;width:100px;font-size:2.3px;line-height:3px">Lorem ipsum dolor sit amet, consectetur adipiscing elit, sed do eiusmod tempor incididunt ut labore et dolore magna aliqua. Ut enim ad minim veniam, quis nostrud exercitation ullamco laboris nisi ut aliquip ex ea commodo consequat.</p>
</section>

<!-- Row 3 -->
<section class="slide dark" style="left:28px;top:379px">
  <div class="a" style="left:20px;top:37px;width:221px;height:81px;background:var(--paper)"></div>
  <div class="photo" role="img" aria-label="Photo of white jigsaw puzzle pieces" style="left:31px;top:25px;width:104px;height:104px;background:linear-gradient(135deg,#f4f4f4,#d7d7d7 55%,#9a9a9a)"></div>
  <p class="a" style="left:139px;top:50px;font-size:6.5px;font-weight:600;color:var(--ink)">RECOMMENDED SOLUTION</p>
  <div class="rule" style="left:139px;top:60px;width:123px"></div>
  <p class="tx" style="left:150px;top:66px;width:77px;text-align:right;color:#333">Lorem ipsum dolor sit amet, consectetur adipiscing elit, sed do eiusmod tempor incididunt ut labore et dolore magna aliqua. Ut enim ad minim veniam, quis nostrud exercitation ullamco laboris nisi ut aliquip ex ea commodo consequat. Duis aute irure dolor in reprehenderit in voluptate velit esse cillum dolore eu fugiat nulla pariatur. Excepteur sint occaecat cupidatat non proident, sunt in culpa qui officia deserunt mollit anim id est laborum.</p>
</section>

<section class="slide dark" style="left:312px;top:379px">
  <p class="a wide" style="left:0;width:262px;text-align:center;top:15px;font-size:8px;letter-spacing:1px;line-height:10px">WHY THIS OPTION<br>(EVALUATION SUMMARY)</p>
  <div class="cell" style="left:38px;top:42px;width:70px;height:17px;font-size:4px">CRITERIA</div>
  <div class="cell" style="left:110px;top:42px;width:43px;height:17px;font-size:4px">Option 1</div>
  <div class="cell" style="left:155px;top:42px;width:30px;height:17px;font-size:4px">Option 2</div>
  <div class="cell" style="left:187px;top:42px;width:37px;height:17px;font-size:4px">Option 3</div>
  <div class="cell" style="left:38px;top:62px;width:70px;height:14px">Strategic alignment</div>
  <div class="cell" style="left:110px;top:62px;width:43px;height:14px">Low</div>
  <div class="cell" style="left:155px;top:62px;width:30px;height:14px">Medium</div>
  <div class="cell" style="left:187px;top:62px;width:37px;height:14px">High</div>
  <div class="cell" style="left:38px;top:78px;width:70px;height:14px">Governance strength</div>
  <div class="cell" style="left:110px;top:78px;width:43px;height:14px">Low</div>
  <div class="cell" style="left:155px;top:78px;width:30px;height:14px">Medium</div>
  <div class="cell" style="left:187px;top:78px;width:37px;height:14px">High</div>
  <div class="cell" style="left:38px;top:94px;width:70px;height:14px">Execution certainty</div>
  <div class="cell" style="left:110px;top:94px;width:43px;height:14px">Low</div>
  <div class="cell" style="left:155px;top:94px;width:30px;height:14px">Medium</div>
  <div class="cell" style="left:187px;top:94px;width:37px;height:14px">High</div>
  <div class="cell" style="left:38px;top:110px;width:70px;height:14px">Risk management</div>
  <div class="cell" style="left:110px;top:110px;width:43px;height:14px">Low</div>
  <div class="cell" style="left:155px;top:110px;width:30px;height:14px">Medium</div>
  <div class="cell" style="left:187px;top:110px;width:37px;height:14px">High</div>
</section>

<section class="slide dark" style="left:612px;top:379px">
  <div class="a" style="left:18px;top:0;width:100px;height:148px;background:var(--paper)"></div>
  <p class="h" style="left:32px;top:32px;font-size:10px;font-weight:800;color:var(--ink)">Key Risks &amp;</p>
  <p class="h wide" style="left:32px;top:44px;font-size:11px;letter-spacing:.8px;font-weight:600;color:var(--ink)">MITIGATIONS</p>
  <div class="rule" style="left:0;top:60px;width:118px"></div>
  <p class="tx" style="left:32px;top:66px;width:68px;color:#333">Lorem ipsum dolor sit amet, consectetur adipiscing elit, sed do eiusmod tempor incididunt ut labore et dolore magna aliqua. Ut enim ad minim veniam, quis nostrud exercitation ullamco laboris nisi ut aliquip ex ea commodo consequat. Duis aute irure dolor in reprehenderit in voluptate velit esse cillum dolore eu fugiat nulla pariatur. Excepteur sint occaecat cupidatat non proident, sunt in culpa qui officia deserunt mollit anim id est laborum.</p>
  <div class="photo" role="img" aria-label="Photo of calculator and financial charts" style="left:129px;top:20px;width:114px;height:53px;background:linear-gradient(135deg,#2f6f9c,#5fb3dd 60%,#a9def2)"></div>
  <div class="photo" role="img" aria-label="Photo of grey puzzle with a blue risk piece" style="left:129px;top:75px;width:114px;height:53px;background:linear-gradient(135deg,#6d6d6d,#b9b9b9 55%,#7a7a7a)"></div>
</section>

<section class="slide dark" style="left:910px;top:379px">
  <p class="h" style="left:27px;top:22px;font-size:16px;font-weight:700;line-height:16px">Financial &amp;<br>Resource Impact</p>
  <div class="rule" style="left:0;top:73px;width:262px"></div>
  <div class="card" style="left:27px;top:60px;width:93px;height:65px"></div>
  <div class="card" style="left:137px;top:60px;width:93px;height:65px"></div>
  <p class="a" style="left:27px;top:63px;width:93px;text-align:center;font-size:5.5px;font-weight:700;color:var(--ink)">Financial Impact</p>
  <p class="a" style="left:137px;top:63px;width:93px;text-align:center;font-size:5.5px;font-weight:700;color:var(--ink)">Resource Impact</p>
  <div class="rule" style="left:0;top:73px;width:262px"></div>
  <p class="tx" style="left:48px;top:79px;width:52px;text-align:center;color:#333">Lorem ipsum dolor sit amet, consectetur adipiscing elit. In neque nunc, molestie eu semper id, auctor quis metus. Maecenas mattis metus sapien, vitae ultricies nunc ornare vitae.</p>
  <p class="tx" style="left:158px;top:79px;width:52px;text-align:center;color:#333">Lorem ipsum dolor sit amet, consectetur adipiscing elit. In neque nunc, molestie eu semper id, auctor quis metus. Maecenas mattis metus sapien, vitae ultricies nunc ornare vitae.</p>
</section>

<!-- Row 4 -->
<section class="slide dark" style="left:28px;top:546px">
  <div class="a" style="left:20px;top:37px;width:221px;height:81px;background:var(--paper)"></div>
  <div class="photo" role="img" aria-label="Photo of governance word collage in blue" style="left:31px;top:25px;width:104px;height:104px;background:linear-gradient(135deg,#0e3f86,#2d86d6 50%,#0b2d63)"></div>
  <p class="a" style="left:139px;top:43px;width:94px;text-align:right;font-size:6.5px;font-weight:600;line-height:7px;color:var(--ink)">GOVERNANCE &amp;<br>ACCOUNTABILITY</p>
  <div class="rule" style="left:139px;top:60px;width:123px"></div>
  <p class="tx" style="left:150px;top:66px;width:83px;text-align:right;color:#333">Lorem ipsum dolor sit amet, consectetur adipiscing elit, sed do eiusmod tempor incididunt ut labore et dolore magna aliqua. Ut enim ad minim veniam, quis nostrud exercitation ullamco laboris nisi ut aliquip ex ea commodo consequat. Duis aute irure dolor in reprehenderit in voluptate velit esse cillum dolore eu fugiat nulla pariatur. Excepteur sint occaecat cupidatat non proident, sunt in culpa qui officia deserunt mollit anim id est laborum.</p>
</section>

<section class="slide" style="left:312px;top:546px">
  <div class="wave" role="img" aria-label="Soft flowing line pattern" style="left:200px;top:-20px;width:100px;height:190px"></div>
  <div class="frame" style="left:23px;top:20px;width:219px;height:108px"></div>
  <p class="h" style="left:0;width:262px;text-align:center;top:38px;font-size:9.5px;font-weight:600">IMPLEMENTATION PLAN &amp; TIMELINE</p>
  <div class="a" style="left:64px;top:60px;width:137px;height:1px;background:var(--indigo)"></div>
  <div class="dot" style="left:87px;top:58px"></div><div class="dot" style="left:129px;top:58px"></div><div class="dot" style="left:170px;top:58px"></div>
  <p class="a" style="left:69px;top:71px;width:40px;text-align:center;font-size:3px;font-weight:700;line-height:3.3px">PHASE 1 –<br>MOBILISATION<br>(0–30 DAYS)</p>
  <p class="a" style="left:110px;top:71px;width:40px;text-align:center;font-size:3px;font-weight:700;line-height:3.3px">PHASE 2 –<br>DESIGN &amp;<br>ALIGNMENT<br>(30–90 DAYS)</p>
  <p class="a" style="left:151px;top:71px;width:40px;text-align:center;font-size:3px;font-weight:700;line-height:3.3px">PHASE 3 –<br>EXECUTION &amp;<br>EMBED<br>(90–180 DAYS)</p>
  <p class="tx" style="left:71px;top:89px;width:36px;text-align:center;font-size:2.2px;line-height:2.9px">Lorem ipsum dolor sit amet, consectetur adipiscing elit, sed do eiusmod tempor incididunt ut labore et dolore magna aliqua. Ut enim ad minim veniam, quis nostrud exercitation ullamco laboris nisi ut aliquip ex ea commodo consequat.</p>
  <p class="tx" style="left:112px;top:89px;width:36px;text-align:center;font-size:2.2px;line-height:2.9px">Lorem ipsum dolor sit amet, consectetur adipiscing elit, sed do eiusmod tempor incididunt ut labore et dolore magna aliqua. Ut enim ad minim veniam, quis nostrud exercitation ullamco laboris nisi ut aliquip ex ea commodo consequat.</p>
  <p class="tx" style="left:153px;top:89px;width:36px;text-align:center;font-size:2.2px;line-height:2.9px">Lorem ipsum dolor sit amet, consectetur adipiscing elit, sed do eiusmod tempor incididunt ut labore et dolore magna aliqua. Ut enim ad minim veniam, quis nostrud exercitation ullamco laboris nisi ut aliquip ex ea commodo consequat.</p>
</section>

<section class="slide" style="left:610px;top:546px">
  <div class="wave" role="img" aria-label="Soft flowing line pattern" style="left:20px;top:90px;width:200px;height:80px"></div>
  <svg class="a" style="left:43px;top:40px" width="56" height="56" viewBox="0 0 56 56" role="img" aria-label="Donut chart, five elements at 20% each">
    <g fill="none" stroke-width="10">
      <circle cx="28" cy="28" r="23" stroke="#111" stroke-dasharray="28.9 144.5" transform="rotate(-90 28 28)"/>
      <circle cx="28" cy="28" r="23" stroke="#2c2c2c" stroke-dasharray="28.9 144.5" transform="rotate(-18 28 28)"/>
      <circle cx="28" cy="28" r="23" stroke="#4a4a4a" stroke-dasharray="28.9 144.5" transform="rotate(54 28 28)"/>
      <circle cx="28" cy="28" r="23" stroke="#6e6e6e" stroke-dasharray="28.9 144.5" transform="rotate(126 28 28)"/>
      <circle cx="28" cy="28" r="23" stroke="#959595" stroke-dasharray="28.9 144.5" transform="rotate(198 28 28)"/>
    </g>
  </svg>
  <p class="a" style="left:78px;top:26px;font-size:2.4px;font-weight:700;text-align:center;line-height:2.8px">Element 1<br>20%</p>
  <p class="a" style="left:109px;top:66px;font-size:2.4px;font-weight:700;text-align:center;line-height:2.8px">Element 2<br>20%</p>
  <p class="a" style="left:64px;top:99px;font-size:2.4px;font-weight:700;text-align:center;line-height:2.8px">Element 3<br>20%</p>
  <p class="a" style="left:24px;top:66px;font-size:2.4px;font-weight:700;text-align:center;line-height:2.8px">Element 4<br>20%</p>
  <p class="a" style="left:41px;top:26px;font-size:2.4px;font-weight:700;text-align:center;line-height:2.8px">Element 5<br>20%</p>
  <p class="h" style="left:153px;top:27px;font-size:10px;font-weight:800">Key</p>
  <p class="h wide" style="left:153px;top:38px;font-size:13px;letter-spacing:1px;font-weight:600">MILESTONES</p>
  <div class="rule" style="left:150px;top:57px;width:112px"></div>
  <p class="tx" style="left:153px;top:63px;width:78px">Lorem ipsum dolor sit amet, consectetur adipiscing elit, sed do eiusmod tempor incididunt ut labore et dolore magna aliqua. Ut enim ad minim veniam, quis nostrud exercitation ullamco laboris nisi ut aliquip ex ea commodo consequat. Duis aute irure dolor in reprehenderit in voluptate velit esse cillum dolore eu fugiat nulla pariatur. Excepteur sint occaecat cupidatat non proident, sunt in culpa qui officia deserunt mollit anim id est laborum.</p>
</section>

<section class="slide dark" style="left:910px;top:546px">
  <div class="a" style="left:24px;top:0;width:1px;height:148px;background:rgba(255,255,255,.6)"></div>
  <p class="a wide" style="left:31px;top:14px;font-size:7px;letter-spacing:1.6px">TORVANE</p>
  <p class="a" style="left:7px;top:138px;font-size:2.6px;transform:rotate(-90deg);transform-origin:left top;white-space:nowrap">www.torvaneadvisory.example</p>
  <div class="a" style="left:139px;top:38px;width:98px;height:29px;border:1px solid #fff;display:flex;align-items:center;justify-content:center;font-size:15px;font-weight:600;letter-spacing:.8px">CONTACT</div>
  <p class="a" style="left:100px;top:75px;width:132px;text-align:right;font-size:3px;font-weight:700">www.torvaneadvisory.example</p>
  <p class="a" style="left:100px;top:86px;width:132px;text-align:right;font-size:3px;font-weight:700">hello@torvaneadvisory.example</p>
  <p class="a" style="left:100px;top:97px;width:132px;text-align:right;font-size:3px;font-weight:700">+61 2 5550 1842</p>
  <p class="a" style="left:100px;top:107px;width:132px;text-align:right;font-size:3px;font-weight:700;line-height:3.6px">48 Harbour Rd, Eastbay,<br>NSW 2031</p>
  <svg class="a" style="left:234px;top:74px" width="8" height="44" viewBox="0 0 8 44" fill="none" stroke="#fff" stroke-width=".8">
    <circle cx="4" cy="4" r="3.4" fill="#fff"/><path d="M1 4h6M4 1v6" stroke="#1c2e38" stroke-width=".6"/>
    <circle cx="4" cy="15" r="3.4" fill="#fff"/><rect x="2" y="13.6" width="4" height="2.8" stroke="#1c2e38" stroke-width=".5"/>
    <circle cx="4" cy="26" r="3.4" fill="#fff"/><path d="M2.6 24.4c.3 1.9 1.2 2.8 3 3.2" stroke="#1c2e38" stroke-width=".8"/>
    <path d="M4 33c-1.7 0-3 1.3-3 3 0 2.1 3 5 3 5s3-2.9 3-5c0-1.7-1.3-3-3-3z" fill="#fff"/><circle cx="4" cy="36" r=".9" fill="#1c2e38" stroke="none"/>
  </svg>
</section>

<!-- Row 5 -->
<section class="slide" style="left:28px;top:714px">
  <div class="wave" role="img" aria-label="Soft flowing line pattern" style="left:200px;top:-20px;width:100px;height:190px"></div>
  <div class="frame" style="left:23px;top:19px;width:219px;height:109px"></div>
  <p class="h" style="left:0;width:262px;text-align:center;top:38px;font-size:9.5px;font-weight:600">KEY MILESTONES (TIMELINE SLIDE)</p>
  <div class="a" style="left:50px;top:61px;width:160px;height:1px;background:var(--indigo)"></div>
  <div class="dot" style="left:48px;top:59px"></div><div class="dot" style="left:90px;top:59px"></div><div class="dot" style="left:131px;top:59px"></div><div class="dot" style="left:173px;top:59px"></div><div class="dot" style="left:208px;top:59px"></div>
  <p class="a" style="left:47px;top:72px;font-size:3px;font-weight:700;line-height:3.4px">BOARD<br>APPROVAL – [DATE]</p>
  <p class="a" style="left:88px;top:72px;font-size:3px;font-weight:700;line-height:3.4px">GOVERNANCE<br>FRAMEWORK<br>ESTABLISHED –<br>[DATE]</p>
  <p class="a" style="left:130px;top:72px;font-size:4px;font-weight:700;line-height:4.3px">FIRST<br>PERFORMANCE<br>REVIEW – [DATE]</p>
  <p class="a" style="left:176px;top:72px;font-size:4px;font-weight:700;line-height:4.3px">FULL<br>IMPLEMENTATION<br>COMPLETE – [DATE]</p>
  <p class="tx" style="left:47px;top:91px;width:36px;font-size:2.2px;line-height:2.9px">Lorem ipsum dolor sit amet, consectetur adipiscing elit, sed do eiusmod tempor incididunt ut labore et dolore magna aliqua. Ut enim ad minim veniam, quis nostrud exercitation ullamco laboris nisi ut aliquip ex ea commodo consequat.</p>
  <p class="tx" style="left:88px;top:91px;width:36px;font-size:2.2px;line-height:2.9px">Lorem ipsum dolor sit amet, consectetur adipiscing elit, sed do eiusmod tempor incididunt ut labore et dolore magna aliqua. Ut enim ad minim veniam, quis nostrud exercitation ullamco laboris nisi ut aliquip ex ea commodo consequat.</p>
  <p class="tx" style="left:130px;top:91px;width:36px;font-size:2.2px;line-height:2.9px">Lorem ipsum dolor sit amet, consectetur adipiscing elit, sed do eiusmod tempor incididunt ut labore et dolore magna aliqua. Ut enim ad minim veniam, quis nostrud exercitation ullamco laboris nisi ut aliquip ex ea commodo consequat.</p>
  <p class="tx" style="left:176px;top:91px;width:36px;font-size:2.2px;line-height:2.9px">Lorem ipsum dolor sit amet, consectetur adipiscing elit, sed do eiusmod tempor incididunt ut labore et dolore magna aliqua. Ut enim ad minim veniam, quis nostrud exercitation ullamco laboris nisi ut aliquip ex ea commodo consequat.</p>
</section>

<section class="slide" style="left:312px;top:714px">
  <div class="a" style="left:0;top:0;width:26px;height:148px;background:var(--deep)"></div>
  <div class="a" style="left:236px;top:0;width:26px;height:148px;background:var(--deep)"></div>
  <p class="h" style="left:0;width:262px;text-align:center;top:26px;font-size:11.5px;font-weight:600">DECISION SOUGHT</p>
  <div class="rule" style="left:26px;top:43px;width:210px"></div>
  <div class="icon" style="left:56px;top:49px"></div>
  <div class="icon" style="left:111px;top:49px"></div>
  <div class="icon" style="left:166px;top:49px"></div>
  <svg class="a" style="left:56px;top:49px" width="138" height="28" viewBox="0 0 138 28" fill="none" stroke="#fff" stroke-width="1">
    <rect x="9" y="7" width="8" height="11"/><circle cx="17" cy="18" r="3"/><path d="M19 20l3 3"/>
    <path d="M64 7h7l3 3v11h-10z"/><path d="M66 12h6M66 15h6M66 18h4"/>
    <path d="M113 15l6-5 6 5v7h-12z"/><path d="M114 8a8 8 0 0 1 10 0M116 5.5a11 11 0 0 1 6 0"/>
  </svg>
  <p class="tx" style="left:51px;top:82px;width:50px">Lorem ipsum dolor sit amet, consectetur adipiscing elit, sed do eiusmod tempor incididunt ut labore et dolore magna aliqua. Ut enim ad minim veniam, quis nostrud exercitation ullamco laboris nisi ut aliquip ex ea commodo consequat. Duis aute irure dolor in reprehenderit in voluptate velit esse cillum dolore eu fugiat nulla pariatur.</p>
  <p class="tx" style="left:105px;top:82px;width:50px">Lorem ipsum dolor sit amet, consectetur adipiscing elit, sed do eiusmod tempor incididunt ut labore et dolore magna aliqua. Ut enim ad minim veniam, quis nostrud exercitation ullamco laboris nisi ut aliquip ex ea commodo consequat. Duis aute irure dolor in reprehenderit in voluptate velit esse cillum dolore eu fugiat nulla pariatur.</p>
  <p class="tx" style="left:159px;top:82px;width:50px">Lorem ipsum dolor sit amet, consectetur adipiscing elit, sed do eiusmod tempor incididunt ut labore et dolore magna aliqua. Ut enim ad minim veniam, quis nostrud exercitation ullamco laboris nisi ut aliquip ex ea commodo consequat. Duis aute irure dolor in reprehenderit in voluptate velit esse cillum dolore eu fugiat nulla pariatur.</p>
</section>

<section class="slide" style="left:610px;top:714px">
  <div class="wave" role="img" aria-label="Soft flowing line pattern" style="left:120px;top:-30px;width:160px;height:60px"></div>
  <div class="wave" role="img" aria-label="Soft flowing line pattern" style="left:0;top:120px;width:200px;height:50px"></div>
  <div class="frame" style="left:23px;top:19px;width:101px;height:109px"></div>
  <div class="frame" style="left:132px;top:19px;width:101px;height:109px"></div>
  <div class="rule" style="left:0;top:57px;width:262px"></div>
  <p class="h" style="left:38px;top:37px;font-size:8px;font-weight:800">Next</p>
  <p class="h wide" style="left:38px;top:46px;font-size:8px;letter-spacing:.8px;font-weight:600">STEPS</p>
  <p class="h" style="left:147px;top:37px;font-size:8px;font-weight:800">Questions &amp;</p>
  <p class="h wide" style="left:147px;top:46px;font-size:8px;letter-spacing:.8px;font-weight:600">DISCUSSION</p>
  <p class="tx" style="left:38px;top:64px;width:74px">Lorem ipsum dolor sit amet, consectetur adipiscing elit, sed do eiusmod tempor incididunt ut labore et dolore magna aliqua. Ut enim ad minim veniam, quis nostrud exercitation ullamco laboris nisi ut aliquip ex ea commodo consequat. Duis aute irure dolor in reprehenderit in voluptate velit esse cillum dolore eu fugiat nulla pariatur. Excepteur sint occaecat cupidatat non proident, sunt in culpa qui officia deserunt mollit anim id est laborum.</p>
  <p class="tx" style="left:147px;top:64px;width:74px">Lorem ipsum dolor sit amet, consectetur adipiscing elit, sed do eiusmod tempor incididunt ut labore et dolore magna aliqua. Ut enim ad minim veniam, quis nostrud exercitation ullamco laboris nisi ut aliquip ex ea commodo consequat. Duis aute irure dolor in reprehenderit in voluptate velit esse cillum dolore eu fugiat nulla pariatur. Excepteur sint occaecat cupidatat non proident, sunt in culpa qui officia deserunt mollit anim id est laborum.</p>
</section>

<section class="slide dark portrait" style="left:898px;top:713px">
  <p class="a wide" style="left:14px;top:15px;font-size:8px;letter-spacing:1.6px">TORVANE</p>
  <p class="a" style="left:14px;top:66px;font-size:5.4px">STRATEGIC REVIEW &amp;</p>
  <p class="h wide" style="left:14px;top:72px;font-size:11.5px;line-height:11px">Execution<br>Roadmap</p>
  <div class="a" style="left:14px;top:96px;width:70px;height:1px;background:#fff"></div>
  <p class="a" style="left:14px;top:123px;font-size:3.6px;font-weight:700;line-height:4px">Connecting<br>Strategy,<br>Governance<br>&amp; Execution</p>
</section>

<section class="slide portrait" style="left:1044px;top:713px">
  <div class="wave" role="img" aria-label="Soft flowing line pattern" style="left:-20px;top:20px;width:60px;height:150px"></div>
  <div class="a" style="left:31px;top:0;width:103px;height:172px;background:var(--navy)"></div>
  <div class="a" style="left:31px;top:34px;width:103px;height:1px;background:#fff"></div>
  <p class="a" style="left:42px;top:41px;font-size:5px;font-weight:600;color:#fff">EXECUTIVE SUMMARY</p>
  <p class="tx" style="left:42px;top:51px;width:80px;font-size:2.2px;line-height:2.9px;color:#d8e2ec">Lorem ipsum dolor sit amet, consectetur adipiscing elit, sed do eiusmod tempor incididunt ut labore et dolore magna aliqua. Ut enim ad minim veniam, quis nostrud exercitation ullamco laboris nisi ut aliquip ex ea commodo consequat. Duis aute irure dolor in reprehenderit in voluptate velit esse cillum dolore eu fugiat nulla pariatur.<br><br>Lorem ipsum dolor sit amet, consectetur adipiscing elit, sed do eiusmod tempor incididunt ut labore et dolore magna aliqua. Ut enim ad minim veniam, quis nostrud exercitation ullamco laboris nisi ut aliquip ex ea commodo consequat. Duis aute irure dolor in reprehenderit in voluptate.<br><br>Lorem ipsum dolor sit amet, consectetur adipiscing elit, sed do eiusmod tempor incididunt ut labore et dolore magna aliqua. Ut enim ad minim veniam, quis nostrud exercitation ullamco laboris nisi ut aliquip ex ea commodo consequat.</p>
  <div class="rule" style="left:0;top:160px;width:110px"></div>
</section>

</body>
</html>
```